Website for IT consulting Company

I need a website upgrade, the existing site content is ok, I would also like to add a testimonial page, the site should be something that is easy for us to update content. You use the content from www.kelvanbrook.com as an example. I will also post update logo and artwork. I also need a contact form with some type of validation or captcha.

I added Coded to the Project

Please omit Address maps

Target Market(s)

small business, service oriented companies. We provide IT Consulting, support and mangement

Industry/Entity Type

Information Technology

Coding

Number of Pages Required

1 page

Font styles to use
Serif
Sans Serif

Requirements
Must have
• Contain logo attached, and content from existing web site www.kelvanbrook.com.
• Also need to update content easily, and be movable to different platforms.
• There is a catch phrase
• "Let us worry about your technology…” “ so you don’t have to!”
• Should be included.
Nice to have
• Testimonial page, Project page where we can post new and past projects and pictures
Should not have
• none

```html
<!DOCTYPE html>
<html lang="en">
<head>
<meta charset="utf-8">
<title>Kelvanbrook – IT Solutions that Work for your Business</title>
<link href="https://fonts.googleapis.com/css2?family=Raleway:wght@400;500;600;700&family=Open+Sans:ital,wght@0,400;0,600;1,400&display=swap" rel="stylesheet">
<style>
:root{
  --blue:#1e8fdc;
  --blue-light:#2aa8e6;
  --blue-deep:#1570c8;
  --ink:#2b2b2b;
  --text:#555b61;
  --muted:#8a9096;
  --white:#ffffff;
  --tile-a:#dfe4e9;
  --tile-b:#eaeef1;
  --section-grey:#f0f1f2;
  --footer:#eff1f3;
  --line:#d5d9dd;
}
*{box-sizing:border-box;margin:0;padding:0}
html,body{width:1200px;height:3564px;overflow:hidden}
body{background:var(--white);font-family:"Open Sans",Arial,sans-serif;color:var(--text);position:relative}
h1,h2,h3,h4{font-family:"Raleway","Helvetica Neue",sans-serif;font-weight:500;color:var(--ink)}
a{text-decoration:none;color:inherit}
.section{position:absolute;left:0;width:1200px;overflow:hidden}

/* header */
.site-header{top:0;height:71px;background:var(--white);box-shadow:0 1px 3px rgba(0,0,0,.08);z-index:2}
.brand{position:absolute;left:160px;top:22px;display:flex;align-items:center;gap:10px}
.brand-mark{width:22px;height:22px;border-radius:50%;background:var(--blue)}
.brand-name{font-family:"Raleway",sans-serif;font-weight:700;font-size:20px;letter-spacing:1px;color:var(--blue-deep)}
.main-nav{position:absolute;right:160px;top:0;height:71px;display:flex;align-items:center;gap:0}
.main-nav a{font-family:"Raleway",sans-serif;font-size:12px;font-weight:600;color:#333;padding:0 17px;letter-spacing:.3px}
.main-nav a.active{color:var(--blue)}
.nav-search{margin-left:8px;padding-left:14px;border-left:1px solid var(--line);height:22px;display:flex;align-items:center}

/* hero */
.hero{top:71px;height:509px}
.hero-visual{position:absolute;inset:0;background:radial-gradient(ellipse at 68% 45%,#4a86c8 0%,#1c3f6e 30%,#0c1a2e 58%,#050a12 100%)}
.hero-title{position:absolute;left:160px;top:176px;font-family:"Raleway",sans-serif;font-size:33px;font-weight:500;line-height:44px;color:var(--white)}
.hero-sub{position:absolute;left:163px;top:276px;font-family:"Raleway",sans-serif;font-size:13px;font-weight:600;color:var(--white);letter-spacing:.3px}
.hero-arrow{position:absolute;top:230px}
.hero-arrow.prev{left:36px}.hero-arrow.next{right:36px}

/* intro */
.intro{top:580px;height:449px;background:var(--white)}
.intro-photo{position:absolute;right:0;top:0;width:650px;height:449px;background:linear-gradient(135deg,#eef1f3 0%,#cfd8e0 45%,#8fa3b5 70%,#dfe5ea 100%);clip-path:polygon(14% 0,100% 0,100% 100%,0 100%)}
.intro-copy{position:absolute;left:160px;top:92px;width:370px}
.intro-copy h2{font-size:28px;line-height:38px;font-weight:500;margin-bottom:26px}
.intro-copy p{font-size:11.5px;line-height:23px}
.text-link{display:block;margin-top:30px;font-family:"Raleway",sans-serif;font-size:12px;font-weight:600;color:var(--blue);letter-spacing:.4px}

/* features */
.features{top:1029px;height:373px;background:linear-gradient(100deg,var(--blue-light) 0%,var(--blue-deep) 100%)}
.feature{position:absolute;top:78px;width:240px;color:var(--white)}
.feature svg{display:block;height:86px;width:86px}
.feature h3{color:var(--white);font-size:16px;font-weight:500;line-height:24px;margin-top:14px}
.feature p{font-size:10.5px;line-height:21px;margin-top:18px;color:rgba(255,255,255,.92)}

/* support grid */
.support{top:1402px;height:511px;background:var(--section-grey)}
.section-title{text-align:center;font-size:27px;font-weight:500}
.support .section-title{margin-top:56px}
.support-grid{position:absolute;left:162px;top:130px;width:876px;display:grid;grid-template-columns:repeat(5,1fr);grid-template-rows:152px 152px}
.support-tile{display:flex;flex-direction:column;align-items:center;justify-content:flex-start;padding-top:30px;text-align:center;font-size:12.5px;line-height:18px;color:#444}
.support-tile svg{width:42px;height:42px;margin-bottom:12px}
.tile-a{background:var(--tile-a)}.tile-b{background:var(--tile-b)}

/* tagline */
.tagline{top:1913px;height:534px;background:var(--white)}
.tagline .section-title{margin-top:72px;font-size:30px}
.tagline-text{width:880px;margin:24px auto 0;text-align:center;font-size:10.5px;line-height:22px}
.tagline-gallery{position:absolute;top:218px;left:162px;display:flex;gap:27px}
.gallery-item{width:274px;height:238px}
.g-cloud{background:linear-gradient(160deg,#cfe6f7 0%,#3b8fd6 55%,#0e3f7a 100%)}
.g-desk{background:linear-gradient(160deg,#e8ecee 0%,#b6c2cb 50%,#5e7283 100%)}
.g-call{background:linear-gradient(160deg,#f2f2f0 0%,#c9c6c0 50%,#4d4a48 100%)}

/* testimonials */
.testimonials{top:2447px;height:345px;background:linear-gradient(100deg,var(--blue-light) 0%,var(--blue-deep) 100%)}
.testimonials .section-title{color:var(--white);margin-top:50px;font-size:28px}
.testimonial-avatar{position:absolute;left:302px;top:121px;width:100px;height:100px;border-radius:50%;border:4px solid var(--white);background:linear-gradient(160deg,#c9a78c,#6d4f3d)}
.testimonial-quote{position:absolute;left:438px;top:132px;width:520px;font-style:italic;font-size:11.5px;line-height:24px;color:rgba(255,255,255,.93)}
.testimonial-quote .q{font-family:Georgia,serif;font-style:normal;font-weight:700;font-size:15px}
.testimonial-author{position:absolute;left:438px;top:238px;font-size:12.5px;color:var(--white)}
.slider-dots{position:absolute;left:580px;top:307px;display:flex;gap:6px}
.slider-dots span{width:6px;height:6px;border-radius:50%;background:rgba(255,255,255,.5)}
.slider-dots span.on{background:var(--white)}

/* about */
.about{top:2792px;height:444px;background:var(--white)}
.about-photo{position:absolute;right:0;top:0;width:560px;height:444px;background:linear-gradient(150deg,#f4f2ef 0%,#e2ddd6 40%,#b9b3ab 70%,#eeeae4 100%);clip-path:polygon(10% 0,100% 0,100% 100%,0 100%)}
.about-copy{position:absolute;left:160px;top:102px;width:390px}
.about-copy h2{font-size:27px;line-height:38px;font-weight:500;margin-bottom:22px}
.about-copy p{font-size:11px;line-height:23px}
.about-copy .text-link{margin-top:28px}

/* footer */
.site-footer{top:3236px;height:328px;background:var(--footer)}
.footer-brand{position:absolute;left:162px;top:60px;width:210px}
.footer-brand .brand{position:static}
.footer-brand p{font-size:10.5px;line-height:20px;margin-top:18px}
.footer-col{position:absolute;top:52px}
.footer-col h4{font-size:12.5px;font-weight:700;letter-spacing:.4px;color:#333;margin-bottom:14px}
.footer-col li{list-style:none;font-size:10.5px;line-height:23px;color:#555}
.footer-bottom{position:absolute;left:160px;top:257px;width:880px;border-top:1px solid var(--line);display:flex;justify-content:space-between;align-items:center;padding-top:16px}
.socials{display:flex;gap:8px}
.socials span{width:24px;height:24px;border-radius:50%;border:1.5px solid #666}
.copyright{font-size:10.5px;color:#555}
</style>
</head>
<body>

<header class="section site-header">
  <a class="brand" href="#"><span class="brand-mark"></span><span class="brand-name">KELVANBROOK</span></a>
  <nav class="main-nav">
    <a class="active" href="#">HOME</a><a href="#">SERVICES</a><a href="#">ABOUT</a><a href="#">SUPPORT</a><a href="#">CLIENTS</a><a href="#">CAREERS</a><a href="#">CONTACT</a>
    <span class="nav-search"><svg width="13" height="13" viewBox="0 0 13 13"><circle cx="5.5" cy="5.5" r="4" fill="none" stroke="#333" stroke-width="1.6"/><line x1="8.5" y1="8.5" x2="12" y2="12" stroke="#333" stroke-width="1.6"/></svg></span>
  </nav>
</header>

<section class="section hero">
  <div class="hero-visual" role="img" aria-label="Hand holding a glowing laptop surrounded by network and email icons over a world map"></div>
  <h1 class="hero-title">IT Solutions that<br>Work for your Business.</h1>
  <p class="hero-sub">A FULL SERVICE TECHNOLOGY COMPANY</p>
  <svg class="hero-arrow prev" width="22" height="48" viewBox="0 0 22 48"><polyline points="20,2 2,24 20,46" fill="none" stroke="#fff" stroke-width="2.5"/></svg>
  <svg class="hero-arrow next" width="22" height="48" viewBox="0 0 22 48"><polyline points="2,2 20,24 2,46" fill="none" stroke="#fff" stroke-width="2.5"/></svg>
</section>

<section class="section intro">
  <div class="intro-photo" role="img" aria-label="Man working at a laptop in a bright office"></div>
  <div class="intro-copy">
    <h2>Flexible solutions for your business needs</h2>
    <p>Kelvanbrook is a technology solution provider based in Houston, Texas. Our goal is to make technology a non-issue for individuals and small to medium size businesses ranging from 5 to 150 Users. Kelvanbrook has the experience, the tools, high-level technology solutions and training to power your business and your work force. We understand that all business's have one goal in common!</p>
    <a class="text-link" href="#">A RETURN ON INVESTMENT</a>
  </div>
</section>

<section class="section features">
  <div class="feature" style="left:160px">
    <svg viewBox="0 0 86 86" fill="#fff"><circle cx="46" cy="24" r="11"/><circle cx="46" cy="24" r="4.5" fill="#2499e0"/><g stroke="#fff" stroke-width="5"><line x1="46" y1="8" x2="46" y2="40"/><line x1="30" y1="24" x2="62" y2="24"/><line x1="35" y1="13" x2="57" y2="35"/><line x1="57" y1="13" x2="35" y2="35"/></g><circle cx="46" cy="24" r="4.5" fill="#2499e0"/><path d="M6 58h14l14 4h18a5 5 0 0 1 0 10H36v2h20l18-10a5 5 0 0 1 6 8L58 84H6z"/></svg>
    <h3>Managed IT Solutions</h3>
    <p>Our staff will design, service, administer and maintain your IT needs. We are well versed on all major operating system, and network appliances.</p>
  </div>
  <div class="feature" style="left:487px">
    <svg viewBox="0 0 86 86" fill="#fff"><circle cx="43" cy="28" r="15"/><path d="M24 30a19 19 0 0 1 38 0" fill="none" stroke="#fff" stroke-width="4"/><rect x="20" y="26" width="7" height="12" rx="3"/><rect x="59" y="26" width="7" height="12" rx="3"/><path d="M14 84c0-18 12-28 29-28s29 10 29 28z"/></svg>
    <h3>Remote Diagnostic<br>and Support</h3>
    <p>Do you need a quick solution to a technical problem? With our free remote assistance tool, a member of our support team.</p>
  </div>
  <div class="feature" style="left:808px">
    <svg viewBox="0 0 86 86" fill="#fff"><circle cx="43" cy="43" r="22"/><g stroke="#fff" stroke-width="9"><line x1="43" y1="10" x2="43" y2="76"/><line x1="10" y1="43" x2="76" y2="43"/><line x1="20" y1="20" x2="66" y2="66"/><line x1="66" y1="20" x2="20" y2="66"/></g><circle cx="43" cy="43" r="10" fill="#2090dc"/><path d="M30 56l-14 14a4 4 0 0 0 6 6l14-14z"/></svg>
    <h3>IT Infrastructure<br>Design and Installation</h3>
    <p>Do you have more than one site? Do you need remote access? We can design and implement LANS/WANS and VPN's.</p>
  </div>
</section>

<section class="section support">
  <h2 class="section-title">IT Support Solutions</h2>
  <div class="support-grid">
    <div class="support-tile tile-a"><svg viewBox="0 0 42 42" fill="#555"><circle cx="18" cy="13" r="8"/><path d="M4 38c0-10 6-15 14-15s14 5 14 15z"/><circle cx="32" cy="30" r="6" fill="#555" stroke="#dfe4e9" stroke-width="2"/></svg>Network<br>Administration</div>
    <div class="support-tile tile-b"><svg viewBox="0 0 42 42" fill="none" stroke="#555" stroke-width="2.5"><rect x="4" y="7" width="34" height="22" rx="1"/><line x1="21" y1="29" x2="21" y2="35"/><line x1="13" y1="36" x2="29" y2="36"/></svg>Desktop Support</div>
    <div class="support-tile tile-a"><svg viewBox="0 0 42 42" fill="none" stroke="#555" stroke-width="2.5"><rect x="6" y="6" width="30" height="20"/><line x1="21" y1="26" x2="21" y2="38"/><line x1="12" y1="32" x2="12" y2="38"/><line x1="30" y1="32" x2="30" y2="38"/><line x1="12" y1="32" x2="30" y2="32"/></svg>Network Cabling</div>
    <div class="support-tile tile-b"><svg viewBox="0 0 42 42" fill="none" stroke="#555" stroke-width="2.5"><path d="M6 20a21 21 0 0 1 30 0"/><path d="M12 25a12 12 0 0 1 18 0"/><rect x="8" y="30" width="26" height="7" fill="#555"/></svg>Wireless Networks</div>
    <div class="support-tile tile-a"><svg viewBox="0 0 42 42" fill="#555"><path d="M21 3l15 6v11c0 10-7 16-15 19C13 36 6 30 6 20V9z"/></svg>Antivirus Solutions</div>
    <div class="support-tile tile-b"><svg viewBox="0 0 42 42" fill="none" stroke="#555" stroke-width="2.5"><circle cx="21" cy="21" r="16"/><ellipse cx="21" cy="21" rx="7" ry="16"/><line x1="5" y1="21" x2="37" y2="21"/></svg>Network Security</div>
    <div class="support-tile tile-a"><svg viewBox="0 0 42 42" fill="none" stroke="#555" stroke-width="2.5"><line x1="21" y1="14" x2="13" y2="38"/><line x1="21" y1="14" x2="29" y2="38"/><line x1="16" y1="28" x2="26" y2="28"/><circle cx="21" cy="12" r="3" fill="#555"/><path d="M13 6a10 10 0 0 0 0 12M29 6a10 10 0 0 1 0 12"/></svg>Telecommunications</div>
    <div class="support-tile tile-b"><svg viewBox="0 0 42 42" fill="#555"><rect x="6" y="6" width="26" height="8"/><rect x="6" y="17" width="26" height="8"/><rect x="6" y="28" width="20" height="8"/><circle cx="32" cy="32" r="6" fill="none" stroke="#555" stroke-width="2.5"/></svg>Disaster Recovery</div>
    <div class="support-tile tile-a"><svg viewBox="0 0 42 42" fill="#555"><rect x="15" y="3" width="12" height="22" rx="6"/><path d="M9 20a12 12 0 0 0 24 0" fill="none" stroke="#555" stroke-width="2.5"/><line x1="21" y1="32" x2="21" y2="38" stroke="#555" stroke-width="2.5"/><line x1="14" y1="38" x2="28" y2="38" stroke="#555" stroke-width="2.5"/></svg>Audio/video<br>Multimedia</div>
    <div class="support-tile tile-b"><svg viewBox="0 0 42 42" fill="none" stroke="#555" stroke-width="2.5"><rect x="4" y="6" width="34" height="24"/><line x1="16" y1="36" x2="26" y2="36"/><line x1="21" y1="30" x2="21" y2="36"/><line x1="14" y1="24" x2="28" y2="12"/></svg>Web Design</div>
  </div>
</section>

<section class="section tagline">
  <h2 class="section-title">Let us worry about your technology…so you don't have to!</h2>
  <p class="tagline-text">Lorem ipsum dolor sit amet, consectetur adipisicing elit, sed do eiusmod tempor incididunt ut labore et dolore magna aliqua. Ut enim ad minim veniam, quis nostrud exercitation ullamco laboris nisi ut aliquip ex ea commodo consequat. Duis aute irure dolor in reprehenderit in voluptate velit esse cillum dolore eu fugiat nulla pariatur.</p>
  <div class="tagline-gallery">
    <div class="gallery-item g-cloud" role="img" aria-label="Cloud computing illustration with connected devices"></div>
    <div class="gallery-item g-desk" role="img" aria-label="Smiling man working on a laptop"></div>
    <div class="gallery-item g-call" role="img" aria-label="Woman on a phone call at her desk"></div>
  </div>
</section>

<section class="section testimonials">
  <h2 class="section-title">Testimonials</h2>
  <div class="testimonial-avatar" role="img" aria-label="Portrait of the client giving the testimonial"></div>
  <p class="testimonial-quote"><span class="q">“</span> Sed ut perspiciatis unde omnis iste natus error sit voluptatem accusantium doloremque laudantium, totam rem aperiam, eaque ipsa quae ab illo inventore veritatis et quasi architecto beatae vitae dicta sunt explicabo. Nemo enim ipsam voluptatem quia voluptas sit aspernat <span class="q">”</span></p>
  <p class="testimonial-author">Head of Fulfillment, City Name</p>
  <div class="slider-dots"><span></span><span class="on"></span><span></span></div>
</section>

<section class="section about">
  <div class="about-photo" role="img" aria-label="Hands typing on a laptop keyboard on a white desk"></div>
  <div class="about-copy">
    <h2>We are Technology<br>Company.</h2>
    <p>Outsourcing is subcontracting a process, such as product design or manufacturing, to a third-party company.[1] The decision to outsource is often made in the interest of lowering firm costs, redirecting or conserving energy directed at the competencies of a particular business, or to make more efficient use of land, labor, capital, (information) technology and resources. Outsourcing became part of the business lexicon during the 1980s.</p>
    <a class="text-link" href="#">READ MORE</a>
  </div>
</section>

<footer class="section site-footer">
  <div class="footer-brand">
    <a class="brand" href="#"><span class="brand-mark"></span><span class="brand-name">KELVANBROOK</span></a>
    <p>Lorem ipsum dolor sit amet, consectetur adipisicing elit, sed do eiusmod tempor incididunt ut labore et dolore magna aliqua.enim ad minim veniam.</p>
  </div>
  <div class="footer-col" style="left:404px"><h4>SITE MAP</h4><ul><li>Managed IT Solutions</li><li>Remote Diagnostic and Support</li><li>IT Infrastructure Design &amp; Installation</li></ul></div>
  <div class="footer-col" style="left:646px"><h4>SERVICES</h4><ul><li>Administration</li><li>Desktop support</li><li>Audio/video Multimedia</li><li>Web design</li><li>Network cabling</li><li>Wireless Networks</li></ul></div>
  <div class="footer-col" style="left:822px"><h4>WHAT WE DO</h4><ul><li>Learning Centre</li><li>Services</li><li>Client Reviews</li><li>Portfolio</li><li>Reviews</li><li>Contact Us</li></ul></div>
  <div class="footer-col" style="left:977px"><h4>LINKS</h4><ul><li>Home</li><li>About</li><li>Services</li><li>Support</li><li>Careers</li><li>Blog</li></ul></div>
  <div class="footer-bottom">
    <div class="socials"><span></span><span></span><span></span><span></span><span></span></div>
    <p class="copyright">Copyright © 2017 Kelvanbrook, All Copyrights reserved</p>
  </div>
</footer>

</body>
</html>
```